Vorelan.com Personal Trainer/Fitness Website

I want a website to market my personal training/Outdoor Bootcamp Class services, as well as to ditribute nutrivex. I need a logo as well I included an address for the Harbor Gales 1975 logo. I'd like Vorelan in place of Harbor Gales, and in Black and white, just different enough so I can't get sued by the PBL.
https://www.pictofind.example/imgres?imgurl=http%3A%2F%2Fwww.darnell-quibury.example%2Fwp-content%2Fuploads%2F2014%2F01%2Fgales_logo4.jpg&imgrefurl=http%3A%2F%2Fwww.darnell-quibury.example%2Fpbl-logo-redesigns-harbor-gales%2F&docid=_qkwzR7TBAgXpL&tbnid=m4tpU8KdOXjnRP%3A&w=600&h=450&client=ms-android-carrier&bih=512&biw=360&ved=0ahUKEwiRtpgyp9HMAhUTwGMKHRPMBWMQMwg6KBQwFA&iact=mrc&uact=8.
It should be about 5 pages 1. home 2. about 3. Services 4. Blog/Videos and programs 5. Contact.
http://www.dorvinfitness.example.uk/ is a website I like the style of.

Target Market(s)

Seattle area

Industry/Entity Type

Fitness

Coding

Coded - Design and coding required

Number of Pages Required

4 page

Font styles to use
Serif
Sans Serif

Requirements
Must have
• A minimal look
Nice to have
• A logo similar to the 1975 Harbor Galewinds Logo, with a Small Milo Brandt ripping his shirt open(with a picture of the logo on his shirt, picture within picture) to turn into Ironjaw in the center. Skyline is black, Background and small figure white(with black logo on shirt)

```html
<!DOCTYPE html>
<html lang="en">
<head>
<meta charset="utf-8">
<title>Vorelan — Personal Training</title>
<link rel="stylesheet" href="https://fonts.googleapis.com/css2?family=Raleway:wght@600;700;800&family=Open+Sans:ital,wght@0,400;0,600;0,700;1,400&display=swap">
<style>
:root{
  --red:#d42a2b;
  --ink:#1f1f24;
  --text:#555;
  --muted:#8a8a8a;
  --hero:#1c2733;
  --footer:#2a2a36;
  --white:#fff;
}
*{box-sizing:border-box;margin:0;padding:0}
html,body{width:1200px;height:3629px;overflow:hidden}
body{font-family:"Open Sans",Arial,sans-serif;color:var(--text);background:var(--white);position:relative}
.abs{position:absolute}
h1,h2,h3,h4{font-family:"Raleway",Arial,sans-serif;color:var(--ink);text-transform:uppercase}
.section-title{font-size:34px;font-weight:800;letter-spacing:3px;text-align:center}
.lead{font-size:12.5px;line-height:25px;text-align:center;color:var(--text)}
.btn{display:inline-block;background:var(--red);color:#fff;font-family:"Raleway",sans-serif;font-weight:700;font-size:13px;letter-spacing:1.5px;text-transform:uppercase;padding:0 24px;height:42px;line-height:42px}
.btn-outline{background:transparent;border:2px solid #fff}

/* header */
.site-header{top:0;left:0;width:1200px;height:85px;background:#fff}
.brand{left:100px;top:14px;display:flex;align-items:center;gap:12px}
.brand-mark{width:54px;height:54px;border-radius:50%;background:var(--ink)}
.brand-name{font-family:"Raleway",sans-serif;font-weight:800;font-size:30px;color:var(--ink);letter-spacing:1px}
.main-nav{right:100px;top:34px;display:flex;gap:56px;font-family:"Raleway",sans-serif;font-weight:700;font-size:12px;letter-spacing:1.5px;color:var(--ink)}

/* hero */
.hero{top:85px;left:0;width:1200px;height:522px;background:linear-gradient(120deg,#2c3c4a 0%,#1a2430 55%,#23303c 100%)}
.hero-text{top:195px;left:0;width:1200px;text-align:center}
.hero-text h1{color:#fff;font-size:40px;font-weight:800;letter-spacing:5px}
.hero-text p{color:#fff;font-family:"Raleway",sans-serif;font-weight:800;font-size:19px;letter-spacing:2px;margin:10px 0 22px;text-transform:uppercase}
.hero-dots{right:26px;top:300px;display:flex;flex-direction:column;gap:20px}
.hero-dots span{width:8px;height:8px;border-radius:50%;background:rgba(255,255,255,.45)}
.hero-dots span.on{background:#fff}

/* welcome */
.welcome{top:665px;left:150px;width:900px;text-align:center}
.welcome .lead{margin:28px 0 32px}

/* services */
.services-title{top:938px;left:0;width:1200px}
.service{top:1036px;width:340px;text-align:center}
.service-icon{width:154px;height:154px;border-radius:50%;background:var(--red);margin:0 auto;display:flex;align-items:center;justify-content:center}
.service h4{font-size:14px;font-weight:700;letter-spacing:2px;margin:36px 0 14px}
.service p{font-size:12.5px;line-height:25px;color:var(--text)}

/* who */
.who-photo{top:1399px;left:0;width:600px;height:455px;background:linear-gradient(135deg,#9aa0a6,#5b5e63 60%,#3e4044)}
.who-panel{top:1399px;left:600px;width:600px;height:455px;background:var(--red);padding:88px 110px 0 110px}
.who-panel h2{color:#fff;font-size:32px;font-weight:800;letter-spacing:2px}
.who-panel p{color:#fff;font-size:12.5px;line-height:26px;margin:22px 0 30px}

/* blog */
.blog-head{top:1912px;left:150px;width:900px;text-align:center}
.blog-head .lead{margin-top:22px}
.post{top:2064px;width:236px;text-align:center}
.post-photo{width:236px;height:226px}
.post h4{font-size:12px;font-weight:800;letter-spacing:1.5px;margin-top:20px}
.post time{display:block;font-size:11.5px;color:var(--text);margin:6px 0 8px}
.post p{font-size:12px;line-height:24px}
.arrow{top:2168px}

/* goals */
.goals{top:2497px;left:0;width:1200px;height:468px;background:linear-gradient(180deg,#2b2b2b,#1c1c1c 60%,#2a2a2a)}
.goals-text{top:2627px;left:190px;width:820px;text-align:center}
.goals-text h2{color:#fff;font-size:34px;font-weight:800;letter-spacing:3px}
.goals-text p{color:#fff;font-size:12.5px;line-height:26px;margin:16px 0 28px}

/* testimonials */
.testi-head{top:3020px;left:150px;width:900px;text-align:center}
.testi-head .lead{margin-top:22px}
.testi-photo{top:3178px;left:172px;width:188px;height:188px;border-radius:50%;background:linear-gradient(135deg,#c9a88d,#8b6d58)}
.quote{top:3210px;left:460px;width:560px}
.quote p{font-style:italic;font-size:12.5px;line-height:25px;color:var(--muted)}
.quote .name{font-family:"Raleway",sans-serif;font-weight:700;font-size:14px;color:var(--red);margin-top:22px}
.quote .role{font-size:11.5px;color:var(--ink);margin-top:4px}
.qmark{font-family:Georgia,serif;font-size:60px;color:#c8c8c8;line-height:1}
.testi-dots{top:3340px;left:1020px;display:flex;gap:5px}
.testi-dots span{width:10px;height:10px;border-radius:50%;border:2px solid #aaa}

/* footer */
.site-footer{top:3439px;left:0;width:1200px;height:190px;background:var(--footer);text-align:center}
.foot-nav{margin-top:46px;display:flex;justify-content:center;gap:52px;font-family:"Raleway",sans-serif;font-weight:700;font-size:11.5px;letter-spacing:1.5px;color:#c9c9d2}
.copy{font-size:11px;color:#9a9aa6;margin-top:14px}
.social{display:flex;justify-content:center;gap:14px;margin-top:22px}
.social span{width:30px;height:30px;border-radius:50%;background:#4a4a58}
.to-top{right:16px;bottom:14px;width:26px;height:22px;background:#3a3a48}
</style>
</head>
<body>

<header class="site-header abs">
  <div class="brand abs"><span class="brand-mark"></span><span class="brand-name">VORELAN</span></div>
  <nav class="main-nav abs"><span>HOME</span><span>ABOUT</span><span>SERVICES</span><span>BLOG</span><span>VIDEOS</span><span>CONTACT</span></nav>
</header>

<section class="hero abs" role="img" aria-label="Athlete doing push-ups on dumbbells in a dark gym"></section>
<div class="hero-text abs">
  <h1>We Are A Personal Training</h1>
  <p>Fitness / Outdoor Bootcamp Class Services</p>
  <span class="btn">Join us now!</span>
</div>
<div class="hero-dots abs"><span></span><span></span><span class="on"></span><span></span></div>

<section class="welcome abs">
  <h2 class="section-title">Welcome to Vorelan</h2>
  <p class="lead">Lorem Ipsum is simply dummy text of the printing and typesetting industry. Lorem Ipsum has been the industry's standard dummy text ever since the 1500s, when an unknown printer took a galley of type and scrambled it to make a type specimen book. It has survived not only five centuries, but also the leap into electronic typesetting, remaining essentially unchanged Lorem Ipsum is simply dummy text of the printing...</p>
  <span class="btn">Join us now</span>
</section>

<h2 class="section-title services-title abs">Personal Training Services</h2>

<div class="service abs" style="left:82px">
  <div class="service-icon">
    <svg width="84" height="84" viewBox="0 0 84 84" fill="none" stroke="#fff" stroke-width="6" stroke-linecap="round" stroke-linejoin="round">
      <circle cx="50" cy="14" r="6" fill="#fff" stroke="none"/>
      <path d="M30 30 L46 24 L40 44 L54 52 L50 66"/><path d="M40 44 L28 58"/><path d="M46 24 L60 34"/>
      <path d="M10 70 L70 70 L76 58"/>
    </svg>
  </div>
  <h4>Personal Training</h4>
  <p>Lorem Ipsum is simply dummy text of the printing and typesetting industry. Lorem Ipsum has been the industry's standard dummy text...</p>
</div>

<div class="service abs" style="left:433px">
  <div class="service-icon">
    <svg width="84" height="84" viewBox="0 0 84 84" fill="none" stroke="#fff" stroke-width="5" stroke-linejoin="round">
      <rect x="10" y="14" width="64" height="44" rx="3"/><path d="M34 58 L32 70 M50 58 L52 70 M24 71 L60 71"/>
    </svg>
  </div>
  <h4>Online Coaching</h4>
  <p>Lorem Ipsum is simply dummy text of the printing and typesetting industry. Lorem Ipsum has been the industry's standard dummy text...</p>
</div>

<div class="service abs" style="left:786px">
  <div class="service-icon">
    <svg width="90" height="84" viewBox="0 0 90 84" fill="#fff">
      <rect x="4" y="36" width="8" height="12" rx="2"/><rect x="14" y="24" width="10" height="36" rx="2"/><rect x="26" y="28" width="8" height="28" rx="2"/>
      <rect x="34" y="38" width="22" height="8"/>
      <rect x="56" y="28" width="8" height="28" rx="2"/><rect x="66" y="24" width="10" height="36" rx="2"/><rect x="78" y="36" width="8" height="12" rx="2"/>
    </svg>
  </div>
  <h4>Small Group</h4>
  <p>Lorem Ipsum is simply dummy text of the printing and typesetting industry. Lorem Ipsum has been the industry's standard dummy text...</p>
</div>

<div class="who-photo abs" role="img" aria-label="Trainer coaching a woman through a barbell squat in the gym"></div>
<section class="who-panel abs">
  <h2>Who we are?</h2>
  <p>Lorem Ipsum is simply dummy text of the printing and typesetting industry. Lorem Ipsum has been the industry's standard dummy text ever since the 1500s, when an unknown printer took a galley of type and scrambled it to make a type specimen book. It has survived not only five centuries, but also the leap into electronic typesetting, remaining essentially unchanged...</p>
  <span class="btn btn-outline">Click here</span>
</section>

<section class="blog-head abs">
  <h2 class="section-title">Blog Posts</h2>
  <p class="lead">Lorem Ipsum is simply dummy text of the printing and typesetting industry. Lorem Ipsum has been the industry's standard dummy text ever since the 1500s, when an unknown printer took a galley of type and scrambled it to make a type specimen book...</p>
</section>

<svg class="arrow abs" style="left:52px" width="20" height="44" viewBox="0 0 20 44" fill="none" stroke="#bbb" stroke-width="2"><path d="M18 2 L3 22 L18 42"/></svg>
<svg class="arrow abs" style="left:1130px" width="20" height="44" viewBox="0 0 20 44" fill="none" stroke="#bbb" stroke-width="2"><path d="M2 2 L17 22 L2 42"/></svg>

<article class="post abs" style="left:99px">
  <div class="post-photo" role="img" aria-label="Muscular athlete posing, black and white" style="background:linear-gradient(135deg,#d8d8d8,#6c6c6c)"></div>
  <h4>Lorem Ipsum is simply</h4><time>Posted on 27 March 2016</time>
  <p>Lorem Ipsum is simply dummy text of the printing and typesetting industry. been the industry...</p>
</article>
<article class="post abs" style="left:356px">
  <div class="post-photo" role="img" aria-label="Women training on exercise bikes" style="background:linear-gradient(135deg,#c9b8a8,#8a5a4e)"></div>
  <h4>Lorem Ipsum is simply</h4><time>Posted on 27 March 2016</time>
  <p>Lorem Ipsum is simply dummy text of the printing and typesetting industry. been the industry...</p>
</article>
<article class="post abs" style="left:612px">
  <div class="post-photo" role="img" aria-label="Athlete lifting dumbbells by a rack" style="background:linear-gradient(135deg,#4a3326,#1b1512)"></div>
  <h4>Lorem Ipsum is simply</h4><time>Posted on 27 March 2016</time>
  <p>Lorem Ipsum is simply dummy text of the printing and typesetting industry. been the industry...</p>
</article>
<article class="post abs" style="left:868px">
  <div class="post-photo" role="img" aria-label="Bodybuilder performing a deadlift" style="background:linear-gradient(135deg,#5a4a42,#211c1a)"></div>
  <h4>Lorem Ipsum is simply</h4><time>Posted on 27 March 2016</time>
  <p>Lorem Ipsum is simply dummy text of the printing and typesetting industry. been the industry...</p>
</article>

<section class="goals abs" role="img" aria-label="Group class exercising with kettlebells in a dim gym"></section>
<div class="goals-text abs">
  <h2>Get to your fitness goals</h2>
  <p>Lorem Ipsum is simply dummy text of the printing and typesetting industry. Lorem Ipsum has been the industry's standard dummy text ever since the 1500s, when an unknown printer took a galley of type and scrambled it to make a type specimen book. It has survived not only five centuries, but also the leap into electronic typesetting, remaining essentially unchanged...</p>
  <span class="btn">Click here</span>
</div>

<section class="testi-head abs">
  <h2 class="section-title">Testimonials</h2>
  <p class="lead">Lorem Ipsum is simply dummy text of the printing and typesetting industry. Lorem Ipsum has been the industry's standard dummy text ever since the 1500s, when an unknown printer took a galley of type and scrambled it to make a type specimen book...</p>
</section>
<div class="testi-photo abs" role="img" aria-label="Portrait of a client"></div>
<span class="qmark abs" style="left:424px;top:3196px">&ldquo;</span>
<span class="qmark abs" style="left:1028px;top:3274px">&rdquo;</span>
<blockquote class="quote abs">
  <p>Lorem Ipsum is simply dummy text of the printing and typesetting industry. Lorem Ipsum has been the industry's standard dummy text ever since the 1500s, when an unknown printer took a galley of type and scrambled it to make a type specimen book...</p>
  <div class="name">Corwin Hale</div>
  <div class="role">Sports man</div>
</blockquote>
<div class="testi-dots abs"><span></span><span></span></div>

<footer class="site-footer abs">
  <nav class="foot-nav"><span>HOME</span><span>ABOUT</span><span>SERVICES</span><span>BLOG</span><span>VIDEO</span><span>CONTACT</span></nav>
  <p class="copy">&copy; 2016 Vorelan. All Rights Reserved</p>
  <div class="social"><span></span><span></span><span></span><span></span><span></span><span></span></div>
  <svg class="to-top abs" viewBox="0 0 26 22"><rect width="26" height="22" fill="#3a3a48"/><path d="M8 13 L13 8 L18 13" stroke="#bbb" stroke-width="2" fill="none"/></svg>
</footer>

</body>
</html>
```